To design a brand identity that is simple and creative with 'Corvane' as the brand name, I like modern simple fonts like helvetica neue, I want to print both sides of the card, I am open to dark front and white back, but the design needs to transfer well to letter heads and email signatures, I am looking for sophisticated and elegant, but open minded about clever and off the wall, I do not do 'boring' Corvane Ventures is the mother company for a small group, specialising in Management & consulting, Software development and construction, we have a high level of integrity, we are transparent and accountable for what we do. my images are provided as a guide only, Im not expecting them to be just copied, Im looking for a creator and passionate thinker, who will put life into their work.

Target Market(s)

usually business minded people who are looking for something different in me, such as leadership, confidence and focus with thinking that is per haps a little outside the box..

Industry/Entity Type

Construction

Requirements
Must have
• clean, minmalistic
Nice to have
• custom logo
Should not have
• boring, traditional

```html
<!DOCTYPE html>
<html lang="en">
<head>
<meta charset="utf-8">
<title>Corvane Ventures – Business Card</title>
<link rel="stylesheet" href="https://fonts.googleapis.com/css2?family=Open+Sans:wght@400;600&display=swap">
<style>
  :root {
    --backdrop: #e6e6ea;
    --card-dark: #1e1e1e;
    --card-dark-edge: #2a2a2a;
    --card-light: #ffffff;
    --accent: #f0642a;
    --panel-start: #d8283a;
    --panel-end: #1d8f82;
    --rule: #b39a96;
    --service-red: #e2483b;
    --bullet-grey: #9a9a9a;
    --muted: #8c8c8c;
    --ink: #2f2f2f;
    --white: #ffffff;
  }
  * { margin: 0; padding: 0; box-sizing: border-box; }
  html, body {
    width: 1200px; height: 987px; overflow: hidden;
    background: var(--backdrop);
    font-family: "Open Sans", Arial, sans-serif;
  }
  .card {
    position: absolute; left: 220px;
    width: 760px; height: 434px;
    border-radius: 30px; overflow: hidden;
    box-shadow: 0 6px 18px rgba(0,0,0,0.18);
  }
  /* Front */
  .card-front {
    top: 38px;
    background: linear-gradient(160deg, var(--card-dark-edge), var(--card-dark) 60%);
  }
  .front-panel { position: absolute; inset: 0; width: 760px; height: 434px; }
  .brand { position: absolute; }
  .front-brand { left: 60px; top: 110px; }
  .wordmark {
    display: flex; align-items: center; gap: 18px;
    font-weight: 600; line-height: 1; letter-spacing: 1px;
  }
  .front-brand .wordmark { font-size: 72px; color: var(--white); }
  .wordmark-square {
    width: 26px; height: 26px; background: var(--accent); flex: none;
  }
  .tagline {
    font-size: 15px; letter-spacing: 3px; text-transform: uppercase;
    color: var(--muted); margin-top: 14px; padding-left: 44px;
  }
  .front-person {
    position: absolute; right: 40px; top: 262px;
    text-align: right; color: var(--white);
  }
  .person-name { font-size: 28px; font-weight: 600; line-height: 1.2; }
  .person-title { font-size: 20px; font-weight: 400; }
  .front-contact {
    position: absolute; left: 40px; bottom: 32px;
    color: var(--white); font-size: 17px; line-height: 1.75;
  }
  .contact-row { display: flex; align-items: center; gap: 10px; }
  .contact-row svg { flex: none; }
  .contact-divider {
    display: inline-block; width: 1px; height: 20px;
    background: var(--white); margin: 0 14px;
  }
  /* Back */
  .card-back {
    top: 514px; background: var(--card-light);
    border: 1px solid #d0d0d0;
  }
  .back-brand { left: 250px; top: 70px; }
  .back-brand .wordmark { font-size: 76px; color: var(--ink); }
  .services {
    position: absolute; left: 110px; top: 236px;
    list-style: none; color: var(--service-red);
    font-size: 21px; line-height: 1.6;
    display: flex; flex-wrap: wrap; width: 560px; column-gap: 22px;
  }
  .services li::before {
    content: "•"; color: var(--bullet-grey); margin-right: 6px;
  }
  .website {
    position: absolute; left: 110px; top: 334px;
    color: var(--ink); font-size: 21px; letter-spacing: 6px;
  }
</style>
</head>
<body>

<section class="card card-front" aria-label="Card front">
  <svg class="front-panel" viewBox="0 0 760 434" aria-hidden="true">
    <defs>
      <linearGradient id="panelGradient" x1="0" y1="0" x2="0" y2="1">
        <stop offset="0" stop-color="var(--panel-start)"/>
        <stop offset="1" stop-color="var(--panel-end)"/>
      </linearGradient>
    </defs>
    <polygon points="410,0 418,0 588,434 580,434" fill="var(--rule)"/>
    <polygon points="430,0 760,0 760,434 600,434" fill="url(#panelGradient)"/>
  </svg>

  <div class="brand front-brand">
    <div class="wordmark"><span class="wordmark-square"></span>Corvane</div>
    <p class="tagline">Integrity in every venture</p>
  </div>

  <div class="front-person">
    <p class="person-name">Your Name</p>
    <p class="person-title">Title</p>
  </div>

  <div class="front-contact">
    <p class="contact-row">
      <svg width="16" height="16" viewBox="0 0 16 16" aria-hidden="true"><circle cx="8" cy="8" r="7.5" fill="#f5b400"/><path d="M5 4.5l1.6-.6 1 2-1 .8c.4 1 1 1.6 2 2l.8-1 2 1-.6 1.6c-2.8.2-5.8-2.8-5.8-5.8z" fill="#1e1e1e"/></svg>
      +61 0400 512 947
    </p>
    <p class="contact-row">
      <svg width="18" height="14" viewBox="0 0 18 14" aria-hidden="true"><rect x="0.5" y="0.5" width="17" height="13" rx="2" fill="#f5b400"/><path d="M2 3l7 5 7-5" fill="none" stroke="#1e1e1e" stroke-width="1.6"/></svg>
      Names@corvane.ventures<span class="contact-divider"></span>Po Box 418 Parth 6031
    </p>
  </div>
</section>

<section class="card card-back" aria-label="Card back">
  <div class="brand back-brand">
    <div class="wordmark"><span class="wordmark-square"></span>Corvane</div>
    <p class="tagline">Integrity in every venture</p>
  </div>
  <ul class="services">
    <li>Management &amp; Consulting</li>
    <li>Software Development</li>
    <li>Construction</li>
  </ul>
  <p class="website">www.corvane.com</p>
</section>

</body>
</html>
```